Animal Eye Clinic needs a Business card

We are a new veterinary ophthalmology practice (Ridgeline Pet Vision Care) and we need a business card designed. We only see animal eyes - we are not a regular veterinary clinic. We already have a logo. We are looking for a professional, good looking business card to hand out to our clients. We are looking for something simple but professional and contemporary. Our logo is likely the only picture/graphic that needs to be on the card.
Updates

Contact Information for Business Card

Delia Vossman, BSc, DVM, MSc, DipACVO
Veterinary Ophthalmologist

Phone: 250.418.3927
Email: ridgelinepetvisioncare@mailbox-example.net
Website: ridgelinepetvisioncare-example.net
Address: 1874 Thornbury Rd
Kelowna, BC, V1X 4M9

Colors

Designer to choose colors to be used in the design.

Requirements
Must have
• Our logo (attached)

```html
<!DOCTYPE html>
<html lang="en">
<head>
<meta charset="utf-8">
<title>Ridgeline Pet Vision Care – Business Card</title>
<link href="https://fonts.googleapis.com/css2?family=Roboto:wght@400;500;700&display=swap" rel="stylesheet">
<style>
  :root {
    --backdrop: #2b2b2b;
    --card: #1f1f1f;
    --card-edge: #2a2a2a;
    --teal: #1a9aa8;
    --text: #e8e8e8;
    --rule: #bdbdbd;
    --faint: rgba(255,255,255,0.045);
  }
  * { box-sizing: border-box; margin: 0; padding: 0; }
  html, body {
    width: 1200px; height: 901px; overflow: hidden;
    background: var(--backdrop);
    font-family: "Roboto", Arial, sans-serif;
  }
  .stage {
    position: relative; width: 1200px; height: 901px;
    display: flex; flex-direction: column; align-items: center;
    justify-content: center; gap: 40px;
  }
  .card {
    position: relative; width: 700px; height: 400px;
    background: var(--card);
    border: 1px solid var(--card-edge);
    overflow: hidden;
  }
  .brand-mark {
    display: flex; align-items: center; gap: 14px;
  }
  .brand-mark .dot {
    flex: none; border-radius: 50%; background: var(--teal);
  }
  .brand-mark .name {
    color: var(--teal); font-weight: 700; text-transform: uppercase;
    line-height: 1.1; letter-spacing: 0.5px;
  }

  /* front */
  .card--front .brand-mark {
    position: absolute; left: 150px; top: 150px;
  }
  .card--front .dot { width: 64px; height: 64px; }
  .card--front .name { font-size: 34px; }
  .card--front .backdrop-shape {
    position: absolute; right: -90px; top: 40px;
    width: 420px; height: 420px; border-radius: 50%;
    background: var(--faint);
  }

  /* back */
  .card--back .brand-mark {
    position: absolute; left: 44px; top: 158px; width: 270px;
  }
  .card--back .dot { width: 40px; height: 40px; }
  .card--back .name { font-size: 21px; }
  .card--back .divider {
    position: absolute; left: 335px; top: 95px;
    width: 1px; height: 200px; background: var(--rule);
  }
  .contact {
    position: absolute; left: 360px; top: 98px; right: 20px;
    color: var(--text); font-size: 15px; line-height: 1.35;
  }
  .contact .person { color: var(--teal); font-weight: 700; font-size: 18px; }
  .contact .credentials { font-weight: 500; font-size: 12px; }
  .contact .role { margin-bottom: 12px; font-size: 16px; }
  .contact .address { margin-bottom: 12px; font-size: 16px; }
  .contact .line { display: flex; align-items: center; gap: 8px; font-size: 14.5px; white-space: nowrap; }
  .contact .line svg { flex: none; width: 13px; height: 13px; fill: var(--teal); }
  .contact .accent { color: var(--teal); }
</style>
</head>
<body>
<main class="stage">
  <section class="card card--front" aria-label="Card front">
    <div class="backdrop-shape" aria-hidden="true"></div>
    <div class="brand-mark">
      <span class="dot" aria-hidden="true"></span>
      <span class="name">Ridgeline Pet<br>Vision Care</span>
    </div>
  </section>

  <section class="card card--back" aria-label="Card back">
    <div class="brand-mark">
      <span class="dot" aria-hidden="true"></span>
      <span class="name">Ridgeline Pet<br>Vision Care</span>
    </div>
    <div class="divider" aria-hidden="true"></div>
    <div class="contact">
      <div><span class="person">Delia Vossman</span><span class="credentials accent">, BSc, DVM, MSc, DipACVO</span></div>
      <div class="role">Veterinary Ophthalmologist</div>
      <div class="address">1874 Thornbury Rd<br>Kelowna, BC, V1X 4M9</div>
      <div class="line">
        <svg viewBox="0 0 24 24" aria-hidden="true"><path d="M6.6 10.8a15.1 15.1 0 0 0 6.6 6.6l2.2-2.2a1 1 0 0 1 1-.25 11.4 11.4 0 0 0 3.6.57 1 1 0 0 1 1 1V20a1 1 0 0 1-1 1A17 17 0 0 1 3 4a1 1 0 0 1 1-1h3.5a1 1 0 0 1 1 1c0 1.25.2 2.45.57 3.57a1 1 0 0 1-.25 1z"/></svg>
        <span>250.418.3927</span>
      </div>
      <div class="line">
        <svg viewBox="0 0 24 24" aria-hidden="true"><path d="M2 5h20v14H2z M3.5 6.5 12 13l8.5-6.5" fill="none" stroke="#1a9aa8" stroke-width="2.2"/></svg>
        <span>ridgelinepetvisioncare@mailbox-example.net</span>
      </div>
      <div class="line">
        <svg viewBox="0 0 24 24" aria-hidden="true"><circle cx="12" cy="12" r="9" fill="none" stroke="#1a9aa8" stroke-width="2.2"/><path d="M3 12h18M12 3c3 3 3 15 0 18M12 3c-3 3-3 15 0 18" fill="none" stroke="#1a9aa8" stroke-width="1.6"/></svg>
        <span>www.<span class="accent">ridgelinepetvisioncare-example</span>.net</span>
      </div>
    </div>
  </section>
</main>
</body>
</html>
```